QRV Advisors needs a web site

We need a web site for www.qrvadvisors-example.com. QRV is a mergers and acquisition consulting company that focuses our buyer and seller services on logistics companies. We help put companies together, and help with legal and financial due diligence. We want the web site to express our service and show the logistics components. We want personalized images versus pictures of trucks and airplanes.

Our new logo uses Burgandy and grey colors. Image attached. We are not in to bold, big letters...classy, artistic, low key preferred. Confidentiality, experience, professional are what we want to express on the site.

All we expect for the first part of this project is a home page, and one subpage.  We are budgeting other funds for the technical aspects of the web site

Reason: All that I'm seeing so far is trucks, forklifts and planes. We are a legal mergers and acquisitions firm that focus on logistics. I like some of the images to say logistics, but really want it say legal, financial, and putting companies together. Will pay extra for the sub page if someone can impress us with a home page.

Reason: Swamped with another project at the moment...will work on this over the weekend and provide designer feedback and select final design by Tuesday

```html
<!DOCTYPE html>
<html lang="en">
<head>
<meta charset="utf-8">
<title>QRV Advisors — Home</title>
<link rel="stylesheet" href="https://fonts.googleapis.com/css2?family=Open+Sans:wght@400;600;700&family=Roboto:wght@500;700&family=Arvo:wght@700&display=swap">
<style>
  :root {
    --burgundy: #a5003a;
    --burgundy-dark: #8c0030;
    --ink: #3a3a3a;
    --text: #444;
    --muted: #777;
    --line: #c9c9c9;
    --band: #3d3d3d;
    --band-dark: #2f2f2f;
    --header-bg: #efefef;
    --white: #fff;
  }
  * { box-sizing: border-box; margin: 0; padding: 0; }
  html, body { width: 1004px; height: 1200px; overflow: hidden; }
  body { position: relative; background: var(--white); font-family: "Open Sans", sans-serif; color: var(--text); }
  .abs { position: absolute; }

  /* Header */
  .site-header { position: absolute; left: 0; top: 0; width: 1004px; height: 122px; background: linear-gradient(90deg, #e9e9e9, #f7f7f7 30%, #efefef); border-top: 6px solid #555; }
  .brand { position: absolute; left: 117px; top: 44px; display: flex; align-items: center; gap: 10px; }
  .brand-mark { width: 14px; height: 14px; background: var(--burgundy); }
  .brand-name { font-size: 28px; font-weight: 600; color: var(--ink); letter-spacing: 0.5px; }
  .call { position: absolute; left: 743px; top: 15px; display: flex; align-items: center; gap: 6px; }
  .call-label { font-size: 11px; color: #333; line-height: 13px; }
  .call-number { font-family: "Roboto", sans-serif; font-weight: 700; font-size: 18px; color: var(--burgundy); line-height: 20px; }
  .main-nav { position: absolute; left: 444px; top: 74px; display: flex; gap: 14px; }
  .main-nav a { display: block; font-size: 11.5px; color: #777; text-decoration: none; padding: 5px 2px 6px; border-top: 1px solid var(--line); border-bottom: 1px solid var(--line); }
  .main-nav a.current { color: var(--burgundy); font-weight: 600; position: relative; }
  .main-nav a.current::before { content: ""; position: absolute; left: 50%; top: -1px; margin-left: -4px; border: 4px solid transparent; border-top-color: #555; }

  /* Hero */
  .hero { position: absolute; left: 0; top: 125px; width: 1004px; height: 371px; background: linear-gradient(100deg, #d9dfe6 0%, #b9c3cf 35%, #8e9aa9 60%, #cfd4da 100%); }
  .hero-arrow { position: absolute; top: 159px; width: 30px; height: 30px; border-radius: 50%; background: rgba(0,0,0,0.75); }
  .hero-caption { position: absolute; left: 545px; top: 253px; width: 459px; height: 72px; background: rgba(40,40,45,0.55); padding: 4px 0 0 61px; font-family: "Arvo", serif; font-weight: 700; font-size: 23px; line-height: 34px; color: var(--white); letter-spacing: 0.8px; }

  /* Services band */
  .services { position: absolute; left: 0; top: 496px; width: 1004px; height: 226px; background: linear-gradient(180deg, var(--band-dark), var(--band) 40%, #444); border-top: 2px solid #555; }
  .service { position: absolute; top: 24px; width: 170px; text-align: center; }
  .service-icon { width: 118px; height: 118px; margin: 0 auto; border-radius: 50%; background: var(--burgundy); display: flex; align-items: center; justify-content: center; }
  .service-title { margin-top: 11px; font-family: "Roboto", sans-serif; font-weight: 500; font-size: 14.5px; color: var(--white); }
  .service-text { margin-top: 5px; font-size: 10px; line-height: 15px; color: #e2e2e2; }
  .band-arrow { position: absolute; top: 68px; }

  /* Content columns */
  .section-title { font-family: "Roboto", sans-serif; font-weight: 700; font-size: 16px; color: #666; padding-bottom: 5px; border-bottom: 1px dashed #aaa; }
  .section-title b { color: var(--burgundy); }
  .col { position: absolute; top: 748px; }
  .about-photo { margin-top: 12px; width: 235px; height: 101px; border: 4px solid var(--burgundy); background: linear-gradient(90deg, #cfc7bf, #e9e4dd 50%, #bdb6b0); }
  .about-text { margin-top: 14px; font-size: 10px; line-height: 15.5px; color: #444; }
  .read-more { display: block; text-align: right; font-size: 10px; font-weight: 700; color: var(--burgundy); text-decoration: none; }
  .news-item { padding: 10px 0 8px; border-bottom: 1px solid #eee; }
  .news-item:last-child { border-bottom: none; }
  .news-meta { font-size: 10px; color: var(--burgundy); }
  .news-text { font-size: 10.5px; line-height: 15.5px; color: #444; letter-spacing: 0.6px; }
  .form-row { display: flex; align-items: flex-start; margin-top: 14px; }
  .form-row label { width: 56px; font-size: 11px; color: #555; padding-top: 2px; }
  .form-row .field { width: 177px; height: 18px; border: 1px solid #bbb; background: var(--white); }
  .form-row .field.message { height: 57px; }
  .submit { margin: 24px 0 0 56px; width: 87px; height: 21px; background: var(--burgundy); color: var(--white); font-family: "Roboto", sans-serif; font-weight: 700; font-size: 13px; display: flex; align-items: center; justify-content: center; }

  /* Footer */
  .site-footer { position: absolute; left: 0; top: 1032px; width: 1004px; height: 168px; background: var(--burgundy); border-top: 4px solid #555; color: var(--white); }
  .foot-title { font-family: "Roboto", sans-serif; font-weight: 500; font-size: 12.5px; padding-bottom: 6px; border-bottom: 1px dashed rgba(255,255,255,0.6); }
  .foot-col { position: absolute; top: 16px; }
  .quick-links li { list-style: none; font-size: 10px; line-height: 18.5px; padding-left: 12px; position: relative; }
  .quick-links li::before { content: "›"; position: absolute; left: 0; top: -1px; }
  .foot-divider { position: absolute; top: 16px; width: 1px; height: 140px; background: rgba(255,255,255,0.25); }
  .foot-contact { display: flex; gap: 14px; font-size: 10px; line-height: 14px; margin-top: 8px; }
  .foot-contact svg { flex: none; }
  .news-copy { font-size: 10px; line-height: 15px; margin-top: 6px; }
  .email-field { margin-top: 5px; width: 169px; height: 19px; background: var(--white); border-radius: 2px; font-size: 10px; color: #888; display: flex; align-items: center; gap: 6px; padding-left: 6px; }
  .subscribe { margin-top: 12px; width: 67px; height: 19px; background: #555; font-weight: 700; font-size: 11px; display: flex; align-items: center; justify-content: center; border-radius: 2px; }
  .foot-brand { position: absolute; left: 710px; top: 14px; width: 177px; text-align: center; font-family: "Open Sans", sans-serif; font-weight: 600; font-size: 56px; line-height: 60px; color: #d9d9d9; letter-spacing: 8px; }
  .social { position: absolute; top: 86px; left: 766px; display: flex; gap: 7px; }
  .social span { width: 21px; height: 21px; border-radius: 3px; background: #dfe6ee; }
  .copyright { position: absolute; left: 700px; top: 118px; width: 205px; text-align: center; font-size: 10px; line-height: 15px; }
</style>
</head>
<body>

<header class="site-header">
  <div class="brand"><span class="brand-mark"></span><span class="brand-name">QRV Advisors</span></div>
  <div class="call">
    <svg width="28" height="28" viewBox="0 0 28 28"><circle cx="14" cy="14" r="12.5" fill="none" stroke="#a5003a" stroke-width="1.5"/><path d="M10 8c-2 2-1 6 3 10s7 4 8 2l-2.5-2.5-2 1c-1-.5-3-2.5-3.5-3.5l1-2L11.5 7z" fill="#a5003a"/></svg>
    <div><div class="call-label">Call Us Today</div><div class="call-number">123 456 7890</div></div>
  </div>
  <nav class="main-nav">
    <a class="current" href="#">Home</a>
    <a href="#">About Us</a>
    <a href="#">Consulting Services</a>
    <a href="#">News &amp; Events</a>
    <a href="#">FAQ's</a>
    <a href="#">Contact Us</a>
  </nav>
</header>

<section class="hero" role="img" aria-label="Photo of three business consultants in conversation in a bright office">
  <span class="hero-arrow" style="left:122px"><svg width="30" height="30" viewBox="0 0 30 30"><path d="M17 9l-6 6 6 6" fill="none" stroke="#fff" stroke-width="1.5"/></svg></span>
  <span class="hero-arrow" style="left:852px"><svg width="30" height="30" viewBox="0 0 30 30"><path d="M13 9l6 6-6 6" fill="none" stroke="#fff" stroke-width="1.5"/></svg></span>
  <div class="hero-caption">We Are A Technology<br>Consulting Company.</div>
</section>

<section class="services">
  <svg class="band-arrow" style="left:95px" width="16" height="30" viewBox="0 0 16 30"><path d="M14 2L3 15l11 13" fill="none" stroke="#888" stroke-width="2"/></svg>
  <svg class="band-arrow" style="left:890px" width="16" height="30" viewBox="0 0 16 30"><path d="M2 2l11 13L2 28" fill="none" stroke="#888" stroke-width="2"/></svg>

  <div class="service" style="left:129px">
    <div class="service-icon"><svg width="64" height="64" viewBox="0 0 64 64" fill="#fff"><rect x="4" y="34" width="4" height="24"/><rect x="11" y="40" width="4" height="18"/><rect x="18" y="30" width="4" height="28"/><rect x="25" y="38" width="4" height="20"/><rect x="32" y="44" width="4" height="14"/><rect x="2" y="58" width="40" height="2"/><circle cx="34" cy="18" r="10" fill="none" stroke="#fff" stroke-width="4"/><path d="M41 25l14 14-3 3-14-14z"/><rect x="30" y="14" width="8" height="10" rx="1"/></svg></div>
    <div class="service-title">Business Analysis</div>
    <div class="service-text">Lorem ipsum dolor sit ameteuis<br>tincidunt ut laoreet amte</div>
  </div>
  <div class="service" style="left:321px">
    <div class="service-icon"><svg width="70" height="50" viewBox="0 0 70 50" fill="#fff"><circle cx="35" cy="10" r="8"/><path d="M22 48V28c0-6 6-9 13-9s13 3 13 9v20z"/><circle cx="13" cy="16" r="6.5"/><path d="M1 48V32c0-5 5-8 12-8 3 0 5 .5 7 1.5-1 1-1.5 3-1.5 5V48z"/><circle cx="57" cy="16" r="6.5"/><path d="M69 48V32c0-5-5-8-12-8-3 0-5 .5-7 1.5 1 1 1.5 3 1.5 5V48z"/></svg></div>
    <div class="service-title">Business Intelligence</div>
    <div class="service-text">Lorem ipsum dolor sit ameteuis<br>tincidunt ut laoreet amte</div>
  </div>
  <div class="service" style="left:513px">
    <div class="service-icon"><svg width="50" height="76" viewBox="0 0 50 76" fill="#fff"><path d="M25 0L40 30H31V42c0 10 8 18 14 24l-6 8c-5-5-11-11-14-17-3 6-9 12-14 17l-6-8c6-6 14-14 14-24V30H10z"/></svg></div>
    <div class="service-title">Mergers</div>
    <div class="service-text">Lorem ipsum dolor sit ameteuis<br>tincidunt ut laoreet amte</div>
  </div>
  <div class="service" style="left:705px">
    <div class="service-icon"><svg width="74" height="58" viewBox="0 0 74 58" fill="#fff"><path d="M46 0l26 22-26 22V32H30V12h16z"/><path d="M28 14L2 36l26 22V46h16V26H28z" stroke="#a5003a" stroke-width="2"/></svg></div>
    <div class="service-title">Acquisition</div>
    <div class="service-text">Lorem ipsum dolor sit ameteuis<br>tincidunt ut laoreet amte</div>
  </div>
</section>

<section class="col" style="left:118px;width:235px">
  <h2 class="section-title"><b>ABOUT</b> COMPANY</h2>
  <div class="about-photo" role="img" aria-label="Group photo of the advisory team"></div>
  <p class="about-text">QRV assists business owners within the logistics industry to implement growth and exit strategies. We offer business planning and merger and acquisition(M&amp;A) advisory services. QRV services are offered by industry executives with extensive M&amp;A experience..</p>
  <a class="read-more" href="#">Read More »</a>
</section>

<section class="col" style="left:386px;width:234px">
  <h2 class="section-title"><b>NEWS &amp;</b> EVENTS</h2>
  <div class="news-item"><div class="news-meta">8-10-2014 | By Admin</div><p class="news-text">Lorem ipsum dolor sit amet, consectetuer adipiscing elit, sed diam...</p><a class="read-more" href="#">Read More »</a></div>
  <div class="news-item"><div class="news-meta">8-10-2014 | By Admin</div><p class="news-text">Lorem ipsum dolor sit amet, consectetuer adipiscing elit, sed diam...</p><a class="read-more" href="#">Read More »</a></div>
  <div class="news-item"><div class="news-meta">8-10-2014 | By Admin</div><p class="news-text">Lorem ipsum dolor sit amet, consectetuer adipiscing elit, sed diam...</p><a class="read-more" href="#">Read More »</a></div>
</section>

<section class="col" style="left:652px;width:235px">
  <h2 class="section-title"><b>CONTACT</b> US</h2>
  <div class="form-row"><label>Name</label><span class="field"></span></div>
  <div class="form-row"><label>Phone</label><span class="field"></span></div>
  <div class="form-row"><label>Email</label><span class="field"></span></div>
  <div class="form-row"><label>Message</label><span class="field message"></span></div>
  <div class="submit">SUBMIT</div>
</section>

<footer class="site-footer">
  <div class="foot-col" style="left:118px;width:111px">
    <h3 class="foot-title">QUICK LINKS</h3>
    <ul class="quick-links" style="margin-top:4px">
      <li>Home</li><li>About Us</li><li>Consulting Services</li><li>News &amp; Events</li><li>FAQ's</li><li>Contact Us</li>
    </ul>
  </div>
  <span class="foot-divider" style="left:244px"></span>
  <div class="foot-col" style="left:272px;width:190px">
    <h3 class="foot-title">CONTACT US</h3>
    <div class="foot-contact"><svg width="14" height="18" viewBox="0 0 14 18"><path d="M7 0a6 6 0 0 1 6 6c0 4-6 12-6 12S1 10 1 6a6 6 0 0 1 6-6z" fill="#fff"/><circle cx="7" cy="6" r="2.2" fill="#a5003a"/></svg><span>Lorem ipsum dolor sit ameteuismo<br>tincidunt ut laoreet dolore my amte,</span></div>
    <div class="foot-contact" style="margin-top:12px"><svg width="14" height="14" viewBox="0 0 14 14"><path d="M3 0c-3 2-3 6 2 10s7 4 9 1l-3-3-2 1.5C7.5 9 5 6.5 4.5 5L6 3z" fill="#fff"/></svg><span>123-456-7890</span></div>
    <div class="foot-contact" style="margin-top:15px"><svg width="16" height="11" viewBox="0 0 16 11"><rect width="16" height="11" fill="#fff"/><path d="M0 0l8 6 8-6" fill="none" stroke="#a5003a" stroke-width="1.2"/></svg><span>info@qrvadvisors-example.com</span></div>
  </div>
  <span class="foot-divider" style="left:489px"></span>
  <div class="foot-col" style="left:513px;width:179px">
    <h3 class="foot-title">NEWSLETTER</h3>
    <p class="news-copy">Subscribe to our newsletter to receive our special offers , discounts &amp; more.</p>
    <div class="email-field"><svg width="13" height="9" viewBox="0 0 13 9"><rect x=".5" y=".5" width="12" height="8" fill="none" stroke="#bbb"/><path d="M.5.5l6 4 6-4" fill="none" stroke="#bbb"/></svg>your e-mail address</div>
    <div class="subscribe">Subscribe</div>
  </div>
  <div class="foot-brand">QRV</div>
  <div class="social" aria-label="Social links"><span></span><span></span><span></span></div>
  <p class="copyright">© 2014 qrvadvisors-example.<br>All Rights Reserved</p>
</footer>

</body>
</html>
```